Corporate Christmas Card Email Template Design

We need a Corporate Christmas Card Design to Email all our customers with our Corporate Logos in it.

Our company deals in Machine Tools & Accessories, you will find out more about us in our web site www.vantoril.com.sg

Vantoril Tools is the distributor, so its logo should be the most prominent followed by the rest of the product logos.

Target Market(s)

Mechanical Engineers

Industry/Entity Type

It Company

Requirements
Must have
• It should not take my customers too long to open the email.

Nice to have
• It will be nice if its humorous.

It would be nice to see moving graphics.

```html
<!DOCTYPE html>
<html lang="en">
<head>
<meta charset="utf-8">
<title>Season's Greetings – Vantoril Tools</title>
<link rel="stylesheet" href="https://fonts.googleapis.com/css2?family=Great+Vibes&family=Roboto+Condensed:wght@700&display=swap">
<style>
  :root {
    --red-deep: #5e0508;
    --red-mid: #9a1a1c;
    --red-glow: #b8322e;
    --gold: #f3cf9a;
    --snow: #ffffff;
    --frost: #f1f3f6;
    --button-grey: #c9c9c9;
    --partner-ink: #2f3a4c;
    --brand-red: #a3222d;
  }
  html, body {
    margin: 0;
    padding: 0;
    width: 1200px;
    height: 807px;
    overflow: hidden;
    background: var(--snow);
  }
  .card {
    position: relative;
    width: 1200px;
    height: 807px;
    background: var(--snow);
    font-family: "Roboto Condensed", sans-serif;
  }
  .greeting-scene {
    position: absolute;
    left: 0;
    top: 0;
    width: 1200px;
    height: 650px;
    background: radial-gradient(ellipse 55% 50% at 50% 40%, var(--red-glow) 0%, var(--red-mid) 45%, var(--red-deep) 100%);
  }
  .frost-frame {
    position: absolute;
    inset: 0;
    box-shadow: inset 0 0 70px 40px var(--frost);
  }
  .snow-forest {
    position: absolute;
    left: 0;
    bottom: 0;
    width: 1200px;
    height: 210px;
    background: linear-gradient(to bottom, rgba(255,255,255,0) 0%, rgba(255,255,255,0.55) 40%, var(--snow) 78%);
  }
  .greeting-text {
    position: absolute;
    margin: 0;
    font-family: "Great Vibes", cursive;
    font-weight: 400;
    color: var(--gold);
    text-shadow: 0 1px 3px rgba(60,0,0,0.5);
    white-space: nowrap;
    line-height: 1;
  }
  .greeting-seasons { left: 244px; top: 200px; font-size: 80px; }
  .greeting-and { left: 530px; top: 300px; font-size: 50px; }
  .greeting-newyear { left: 420px; top: 346px; font-size: 76px; }
  .play-button {
    position: absolute;
    left: 558px;
    top: 458px;
    width: 82px;
    height: 82px;
  }
  .partner {
    position: absolute;
    display: flex;
    align-items: center;
    gap: 8px;
    font-size: 24px;
    font-weight: 700;
    line-height: 1;
    color: var(--partner-ink);
    white-space: nowrap;
  }
  .partner-mark {
    width: 18px;
    height: 18px;
    background: var(--partner-ink);
  }
  .distributor {
    position: absolute;
    left: 810px;
    top: 666px;
    display: flex;
    align-items: center;
    gap: 14px;
    font-size: 44px;
    font-weight: 700;
    line-height: 1;
    color: var(--brand-red);
    white-space: nowrap;
  }
  .distributor-mark {
    width: 42px;
    height: 42px;
    border-radius: 50%;
    background: var(--brand-red);
  }
</style>
</head>
<body>
<main class="card">
  <section class="greeting-scene" role="img" aria-label="Deep red winter night sky framed by frosty snowflakes, with a crescent moon, twinkling stars and snowy pine trees along the bottom">
    <div class="frost-frame"></div>
    <div class="snow-forest"></div>
  </section>

  <h1 class="greeting-text greeting-seasons">Season's Greetings</h1>
  <p class="greeting-text greeting-and">and...</p>
  <p class="greeting-text greeting-newyear">Happy New Year!</p>

  <svg class="play-button" viewBox="0 0 86 86" aria-label="Next">
    <circle cx="43" cy="43" r="41" fill="var(--button-grey)" stroke="#ffffff" stroke-width="3"/>
    <polyline points="36,26 53,43 36,60" fill="none" stroke="#ffffff" stroke-width="7" stroke-linecap="round" stroke-linejoin="round"/>
  </svg>

  <div class="partner" style="left:90px; top:680px;"><span class="partner-mark"></span>Sarvett</div>
  <div class="partner" style="left:230px; top:680px;">Rolvex</div>
  <div class="partner" style="left:364px; top:680px;">Tandor Keil</div>
  <div class="partner" style="left:500px; top:680px;">Kraven</div>
  <div class="partner" style="left:636px; top:680px;">Flexmar</div>

  <div class="partner" style="left:90px; top:738px;">Dornstahl</div>
  <div class="partner" style="left:240px; top:738px;">Holt</div>
  <div class="partner" style="left:362px; top:738px;">Brenkel</div>
  <div class="partner" style="left:480px; top:738px;">Ashgrove</div>
  <div class="partner" style="left:630px; top:738px;">Lindqvar</div>

  <div class="distributor"><span class="distributor-mark"></span>Vantoril Tools</div>
</main>
</body>
</html>
```